FinTech company looking to revamp and expand client-facing interface for our financial models

Pellworth Engines currently has a very simple website that allows clients to interact with our financial models. We are looking to completely redesign the current site and add several extra pages to provide extra functionality. We want the design to have a modern, slick feel, that will work on both a desktop or a tablet. It should be straightforward for clients to move between different pages at any time, and clear from the layout how to interact with the more advanced features. We have included screenshots of existing pages in the attached design brief, as well as sketches of the functionality required by the new pages, but can't provide a direct link to the current site.
Target Market(s)
Professional investors that will be paying to access the interface
Industry/Entity Type
Finance
Number of Pages Required
4 page
Colors
Designer to choose colors to be used in the design.
Look and feel
Each slider illustrates characteristics of the customer's brand and the style your logo design should communicate.

```html
<!DOCTYPE html>
<html lang="en">
<head>
<meta charset="utf-8">
<title>Pellworth Engines – Backtest</title>
<link href="https://fonts.googleapis.com/css2?family=Open+Sans:wght@400;600;700&display=swap" rel="stylesheet">
<style>
:root{
  --ink:#111;
  --teal:#006b66;
  --teal-text:#1c6f6a;
  --nav-bg:#fff;
  --line:#e4e4e4;
  --bg-top:#e6e6e6;
  --bg-bottom:#f9f9f9;
  --head:#1b1b1b;
  --row-alt:#f2f2f2;
  --tab:#fff;
  --tab-active:#cfcfcf;
  --yellow:#b8b63a;
  --blue:#3b6ea9;
  --side:#d9d9d9;
  --navy:#1d3557;
}
*{box-sizing:border-box;margin:0;padding:0}
html,body{width:1200px;height:1094px;overflow:hidden}
body{font-family:"Open Sans",sans-serif;color:var(--ink);position:relative;
  background:linear-gradient(var(--bg-top) 0,#eeeeee 520px,var(--bg-bottom) 568px,var(--bg-bottom) 100%)}
.topnav{position:absolute;left:0;top:0;width:1200px;height:55px;background:var(--nav-bg);box-shadow:0 2px 6px rgba(0,0,0,.08);display:flex}
.brand{width:180px;display:flex;align-items:center;padding-left:67px;font-weight:700;font-size:17px;letter-spacing:.2px}
.navcell{height:55px;border-left:1px solid var(--line);display:flex;align-items:center;justify-content:center;gap:8px;font-weight:700;font-size:13px}
.navcell.range{width:83px}
.navcell.blank{width:125px}
.navcell.models{width:130px}
.navcell.sens{width:163px}
.navcell.port{width:148px}
.navcell.back{width:140px;background:var(--teal);color:#fff;border-left:none}
.navcell.end{flex:1;border-left:1px solid var(--line);border-right:none}
.navcell svg{display:block}

.options{position:absolute;left:0;top:291px;width:46px;height:230px;background:var(--side);border-radius:0 4px 4px 0}
.options span{position:absolute;left:23px;top:115px;transform:translate(-50%,-50%) rotate(-90deg);font-size:15px;font-weight:600;letter-spacing:1px;white-space:nowrap}
.options-btn{position:absolute;left:33px;top:393px;width:27px;height:27px;border-radius:50%;background:var(--navy);border:2px solid #fff;box-shadow:0 0 0 1px #bbb}

.chart-card{position:absolute;left:97px;top:92px;width:1071px;height:393px;background:#fff;border-radius:3px;box-shadow:0 1px 4px rgba(0,0,0,.08);overflow:hidden}
.chart-tabs{height:79px;background:#efefef;position:relative}
.chart-tab{position:absolute;bottom:0;width:83px;height:33px;background:var(--tab);display:flex;align-items:center;justify-content:center;font-size:15px;border-radius:2px 2px 0 0}
.chart-tab.active{background:var(--tab-active);height:41px;padding-bottom:8px}
.chart-plot{position:absolute;left:0;top:79px;width:1071px;height:314px}

.export{position:absolute;top:533px;display:flex;align-items:center;gap:6px;color:var(--teal-text);font-weight:700;font-size:16px}
.export.left{left:382px}
.export.right{left:1084px}

.table-card{position:absolute;top:568px;height:452px;background:#fff;box-shadow:0 2px 5px rgba(0,0,0,.1);overflow:hidden}
.stats{left:97px;width:369px}
.trades{left:503px;width:665px}
.thead{height:64px;background:var(--head);color:#fff;display:flex;font-weight:600;font-size:16px}
.thead div{display:flex;align-items:center;justify-content:center;border-right:1px solid #333}
.trow{height:64.7px;display:flex;font-size:16px}
.trow:nth-child(even){background:var(--row-alt)}
.trow div{display:flex;align-items:center;justify-content:center;border-right:1px solid #ececec}
.scroll{position:absolute;top:64px;right:0;bottom:0;background:#eeeeee}
.stats .scroll{width:37px}
.trades .scroll{width:34px}
.track{position:absolute;left:10px;top:24px;width:18px;height:348px;border-radius:9px;background:#fff;border:1px solid #ccc}
.thumb{position:absolute;left:0;top:0;width:16px;height:68px;border-radius:8px;background:#b3b3b3}
</style>
</head>
<body>

<header class="topnav">
  <div class="brand">PELLWORTH</div>
  <div class="navcell range">250D</div>
  <div class="navcell range">83D</div>
  <div class="navcell range">42D</div>
  <div class="navcell blank"></div>
  <div class="navcell models">
    <svg width="22" height="20" viewBox="0 0 22 20"><path d="M11 1 1 10h3v9h5v-6h4v6h5v-9h3z" fill="none" stroke="#111" stroke-width="2" stroke-linejoin="round"/></svg>MODELS</div>
  <div class="navcell sens">
    <svg width="22" height="22" viewBox="0 0 22 22"><g fill="none" stroke="#111" stroke-width="1.5" stroke-dasharray="2 1.5"><circle cx="11" cy="11" r="9"/><circle cx="11" cy="11" r="5"/></g><circle cx="11" cy="11" r="2" fill="#111"/></svg>SENSITIVITIES</div>
  <div class="navcell port">
    <svg width="22" height="22" viewBox="0 0 22 22"><g fill="none" stroke="#111" stroke-width="1.8"><circle cx="6" cy="6" r="4"/><circle cx="16" cy="6" r="4"/><circle cx="6" cy="16" r="4"/><circle cx="16" cy="16" r="4"/></g></svg>PORTFOLIO</div>
  <div class="navcell back">
    <svg width="24" height="20" viewBox="0 0 24 20"><rect x="1" y="1" width="22" height="18" fill="none" stroke="#fff" stroke-width="1.8"/><path d="M4 15l5-6 4 4 6-8" fill="none" stroke="#fff" stroke-width="1.8"/></svg>BACKTEST</div>
  <div class="navcell end"></div>
</header>

<aside class="options"><span>OPTIONS</span></aside>
<div class="options-btn">
  <svg width="23" height="23" viewBox="0 0 23 23"><path d="M6 11.5h10M12 7l4.5 4.5L12 16" fill="none" stroke="#fff" stroke-width="2"/></svg>
</div>

<section class="chart-card">
  <div class="chart-tabs">
    <div class="chart-tab" style="left:51px">#1</div>
    <div class="chart-tab" style="left:139px">#2</div>
    <div class="chart-tab" style="left:227px">#3</div>
    <div class="chart-tab active" style="left:314px">#4</div>
  </div>
  <svg class="chart-plot" viewBox="105 185 1160 340" preserveAspectRatio="none" role="img" aria-label="Scatter chart of names over time">
    <g stroke="#ececec" stroke-width="1">
      <line x1="190" y1="248" x2="1110" y2="248"/><line x1="190" y1="285" x2="1110" y2="285"/>
      <line x1="190" y1="322" x2="1110" y2="322"/><line x1="190" y1="360" x2="1110" y2="360"/>
      <line x1="190" y1="397" x2="1110" y2="397"/>
      <line x1="217" y1="240" x2="217" y2="435"/><line x1="360" y1="240" x2="360" y2="435"/>
      <line x1="500" y1="240" x2="500" y2="435"/><line x1="640" y1="240" x2="640" y2="435"/>
      <line x1="777" y1="240" x2="777" y2="435"/><line x1="918" y1="240" x2="918" y2="435"/>
      <line x1="1057" y1="240" x2="1057" y2="435"/>
    </g>
    <line x1="185" y1="435" x2="1112" y2="435" stroke="#999" stroke-width="1.2"/>
    <g font-family="Open Sans, sans-serif" font-size="11" fill="#555">
      <text x="186" y="252" text-anchor="end">100</text><text x="186" y="289" text-anchor="end">80</text>
      <text x="186" y="326" text-anchor="end">60</text><text x="186" y="364" text-anchor="end">40</text>
      <text x="186" y="401" text-anchor="end">20</text><text x="186" y="439" text-anchor="end">0</text>
      <g text-anchor="middle"><text x="217" y="461">Jul 2018</text><text x="360" y="461">Sep 2018</text>
      <text x="500" y="461">Nov 2018</text><text x="640" y="461">Jan 2019</text><text x="777" y="461">Mar 2019</text>
      <text x="918" y="461">May 2019</text><text x="1057" y="461">Jul 2019</text></g>
      <text x="1167" y="250" font-family="serif">Names</text>
    </g>
    <line x1="238" y1="248" x2="320" y2="248" stroke="var(--yellow)" stroke-width="7" stroke-linecap="round" stroke-dasharray="0 7"/>
    <line x1="795" y1="250" x2="1063" y2="250" stroke="var(--yellow)" stroke-width="7" stroke-linecap="round" stroke-dasharray="0 7"/>
    <g fill="var(--yellow)">
      <circle cx="322" cy="258" r="3.4"/><circle cx="324" cy="265" r="3.4"/><circle cx="330" cy="262" r="3.4"/><circle cx="334" cy="250" r="3.4"/><circle cx="338" cy="256" r="3.4"/><circle cx="342" cy="252" r="3.4"/><circle cx="346" cy="256" r="3.4"/><circle cx="352" cy="252" r="3.4"/><circle cx="358" cy="254" r="3.4"/><circle cx="366" cy="258" r="3.4"/><circle cx="370" cy="262" r="3.4"/><circle cx="372" cy="314" r="3.4"/><circle cx="376" cy="345" r="3.4"/><circle cx="380" cy="349" r="3.4"/><circle cx="384" cy="326" r="3.4"/><circle cx="386" cy="331" r="3.4"/><circle cx="390" cy="348" r="3.4"/><circle cx="393" cy="347" r="3.4"/><circle cx="397" cy="358" r="3.4"/><circle cx="401" cy="350" r="3.4"/><circle cx="404" cy="345" r="3.4"/><circle cx="408" cy="342" r="3.4"/><circle cx="412" cy="356" r="3.4"/><circle cx="414" cy="306" r="3.4"/><circle cx="417" cy="312" r="3.4"/><circle cx="420" cy="316" r="3.4"/><circle cx="424" cy="289" r="3.4"/><circle cx="428" cy="276" r="3.4"/><circle cx="432" cy="276" r="3.4"/><circle cx="435" cy="248" r="3.4"/><circle cx="440" cy="256" r="3.4"/><circle cx="444" cy="255" r="3.4"/><circle cx="448" cy="321" r="3.4"/><circle cx="451" cy="326" r="3.4"/><circle cx="454" cy="336" r="3.4"/><circle cx="460" cy="343" r="3.4"/><circle cx="464" cy="333" r="3.4"/><circle cx="466" cy="328" r="3.4"/><circle cx="468" cy="410" r="3.4"/><circle cx="472" cy="408" r="3.4"/><circle cx="476" cy="397" r="3.4"/><circle cx="480" cy="410" r="3.4"/><circle cx="484" cy="383" r="3.4"/><circle cx="488" cy="385" r="3.4"/><circle cx="492" cy="414" r="3.4"/><circle cx="496" cy="418" r="3.4"/><circle cx="500" cy="416" r="3.4"/><circle cx="503" cy="426" r="3.4"/><circle cx="507" cy="428" r="3.4"/><circle cx="511" cy="425" r="3.4"/><circle cx="515" cy="417" r="3.4"/><circle cx="520" cy="414" r="3.4"/><circle cx="524" cy="403" r="3.4"/><circle cx="528" cy="392" r="3.4"/><circle cx="532" cy="399" r="3.4"/><circle cx="535" cy="405" r="3.4"/><circle cx="537" cy="384" r="3.4"/><circle cx="541" cy="392" r="3.4"/><circle cx="545" cy="371" r="3.4"/><circle cx="549" cy="378" r="3.4"/><circle cx="552" cy="382" r="3.4"/><circle cx="556" cy="382" r="3.4"/><circle cx="560" cy="387" r="3.4"/><circle cx="562" cy="363" r="3.4"/><circle cx="564" cy="333" r="3.4"/><circle cx="566" cy="322" r="3.4"/><circle cx="570" cy="326" r="3.4"/><circle cx="574" cy="324" r="3.4"/><circle cx="576" cy="252" r="3.4"/><circle cx="580" cy="250" r="3.4"/><circle cx="584" cy="248" r="3.4"/><circle cx="588" cy="250" r="3.4"/><circle cx="592" cy="252" r="3.4"/><circle cx="596" cy="248" r="3.4"/><circle cx="600" cy="254" r="3.4"/><circle cx="603" cy="262" r="3.4"/><circle cx="608" cy="270" r="3.4"/><circle cx="612" cy="421" r="3.4"/><circle cx="616" cy="426" r="3.4"/><circle cx="626" cy="421" r="3.4"/><circle cx="630" cy="419" r="3.4"/><circle cx="634" cy="420" r="3.4"/><circle cx="638" cy="412" r="3.4"/><circle cx="642" cy="408" r="3.4"/><circle cx="646" cy="414" r="3.4"/><circle cx="650" cy="408" r="3.4"/><circle cx="654" cy="414" r="3.4"/><circle cx="658" cy="418" r="3.4"/><circle cx="662" cy="419" r="3.4"/><circle cx="666" cy="414" r="3.4"/><circle cx="670" cy="422" r="3.4"/><circle cx="674" cy="420" r="3.4"/><circle cx="676" cy="409" r="3.4"/><circle cx="678" cy="399" r="3.4"/><circle cx="681" cy="387" r="3.4"/><circle cx="685" cy="381" r="3.4"/><circle cx="688" cy="383" r="3.4"/><circle cx="690" cy="364" r="3.4"/><circle cx="694" cy="350" r="3.4"/><circle cx="696" cy="364" r="3.4"/><circle cx="689" cy="312" r="3.4"/><circle cx="703" cy="312" r="3.4"/><circle cx="706" cy="274" r="3.4"/><circle cx="710" cy="268" r="3.4"/><circle cx="722" cy="270" r="3.4"/><circle cx="726" cy="324" r="3.4"/><circle cx="728" cy="392" r="3.4"/><circle cx="734" cy="393" r="3.4"/><circle cx="738" cy="407" r="3.4"/><circle cx="740" cy="270" r="3.4"/><circle cx="742" cy="305" r="3.4"/><circle cx="744" cy="290" r="3.4"/><circle cx="748" cy="282" r="3.4"/><circle cx="751" cy="294" r="3.4"/><circle cx="756" cy="304" r="3.4"/><circle cx="756" cy="349" r="3.4"/><circle cx="758" cy="262" r="3.4"/><circle cx="763" cy="268" r="3.4"/><circle cx="770" cy="270" r="3.4"/><circle cx="772" cy="262" r="3.4"/><circle cx="776" cy="260" r="3.4"/><circle cx="782" cy="258" r="3.4"/><circle cx="786" cy="262" r="3.4"/><circle cx="790" cy="266" r="3.4"/><circle cx="792" cy="256" r="3.4"/>
    </g>
    <line x1="625" y1="248" x2="1063" y2="248" stroke="var(--blue)" stroke-width="7" stroke-linecap="round" stroke-dasharray="0 7.3"/>
    <g fill="var(--blue)">
      <circle cx="238" cy="314" r="3.4"/><circle cx="240" cy="262" r="3.4"/><circle cx="243" cy="254" r="3.4"/><circle cx="248" cy="260" r="3.4"/><circle cx="252" cy="252" r="3.4"/><circle cx="256" cy="260" r="3.4"/><circle cx="259" cy="329" r="3.4"/><circle cx="262" cy="362" r="3.4"/><circle cx="267" cy="357" r="3.4"/><circle cx="270" cy="375" r="3.4"/><circle cx="273" cy="390" r="3.4"/><circle cx="276" cy="380" r="3.4"/><circle cx="280" cy="370" r="3.4"/><circle cx="283" cy="366" r="3.4"/><circle cx="286" cy="382" r="3.4"/><circle cx="290" cy="325" r="3.4"/><circle cx="293" cy="352" r="3.4"/><circle cx="296" cy="347" r="3.4"/><circle cx="300" cy="350" r="3.4"/><circle cx="304" cy="327" r="3.4"/><circle cx="307" cy="350" r="3.4"/><circle cx="310" cy="390" r="3.4"/><circle cx="314" cy="387" r="3.4"/><circle cx="318" cy="380" r="3.4"/><circle cx="321" cy="350" r="3.4"/><circle cx="324" cy="365" r="3.4"/><circle cx="328" cy="362" r="3.4"/><circle cx="331" cy="355" r="3.4"/><circle cx="335" cy="385" r="3.4"/><circle cx="338" cy="378" r="3.4"/><circle cx="342" cy="382" r="3.4"/><circle cx="345" cy="390" r="3.4"/><circle cx="348" cy="380" r="3.4"/><circle cx="352" cy="390" r="3.4"/><circle cx="355" cy="385" r="3.4"/><circle cx="358" cy="384" r="3.4"/><circle cx="362" cy="390" r="3.4"/><circle cx="366" cy="394" r="3.4"/><circle cx="370" cy="412" r="3.4"/><circle cx="373" cy="414" r="3.4"/><circle cx="377" cy="412" r="3.4"/><circle cx="381" cy="405" r="3.4"/><circle cx="385" cy="415" r="3.4"/><circle cx="388" cy="409" r="3.4"/><circle cx="392" cy="413" r="3.4"/><circle cx="396" cy="412" r="3.4"/><circle cx="400" cy="408" r="3.4"/><circle cx="404" cy="408" r="3.4"/><circle cx="408" cy="412" r="3.4"/><circle cx="412" cy="390" r="3.4"/><circle cx="416" cy="393" r="3.4"/><circle cx="420" cy="389" r="3.4"/><circle cx="424" cy="385" r="3.4"/><circle cx="428" cy="377" r="3.4"/><circle cx="432" cy="380" r="3.4"/><circle cx="436" cy="395" r="3.4"/><circle cx="440" cy="402" r="3.4"/><circle cx="444" cy="392" r="3.4"/><circle cx="448" cy="385" r="3.4"/><circle cx="452" cy="378" r="3.4"/><circle cx="455" cy="399" r="3.4"/><circle cx="458" cy="393" r="3.4"/><circle cx="462" cy="395" r="3.4"/><circle cx="465" cy="381" r="3.4"/><circle cx="469" cy="432" r="3.4"/><circle cx="473" cy="431" r="3.4"/><circle cx="477" cy="414" r="3.4"/><circle cx="481" cy="427" r="3.4"/><circle cx="485" cy="414" r="3.4"/><circle cx="489" cy="405" r="3.4"/><circle cx="493" cy="389" r="3.4"/><circle cx="497" cy="377" r="3.4"/><circle cx="499" cy="304" r="3.4"/><circle cx="501" cy="304" r="3.4"/><circle cx="503" cy="278" r="3.4"/><circle cx="507" cy="273" r="3.4"/><circle cx="511" cy="268" r="3.4"/><circle cx="515" cy="262" r="3.4"/><circle cx="512" cy="285" r="3.4"/><circle cx="518" cy="287" r="3.4"/><circle cx="522" cy="287" r="3.4"/><circle cx="526" cy="284" r="3.4"/><circle cx="530" cy="413" r="3.4"/><circle cx="533" cy="397" r="3.4"/><circle cx="536" cy="407" r="3.4"/><circle cx="540" cy="405" r="3.4"/><circle cx="543" cy="390" r="3.4"/><circle cx="547" cy="388" r="3.4"/><circle cx="551" cy="388" r="3.4"/><circle cx="556" cy="396" r="3.4"/><circle cx="560" cy="401" r="3.4"/><circle cx="562" cy="372" r="3.4"/><circle cx="565" cy="368" r="3.4"/><circle cx="568" cy="353" r="3.4"/><circle cx="571" cy="357" r="3.4"/><circle cx="574" cy="354" r="3.4"/><circle cx="577" cy="268" r="3.4"/><circle cx="580" cy="265" r="3.4"/><circle cx="584" cy="254" r="3.4"/><circle cx="589" cy="256" r="3.4"/><circle cx="593" cy="257" r="3.4"/><circle cx="597" cy="260" r="3.4"/><circle cx="601" cy="261" r="3.4"/><circle cx="607" cy="264" r="3.4"/><circle cx="612" cy="256" r="3.4"/><circle cx="618" cy="248" r="3.4"/><circle cx="622" cy="250" r="3.4"/>
    </g>
    <g fill="#4b9a35"><circle cx="1035" cy="432" r="3.4"/><circle cx="1040" cy="432" r="3.4"/><circle cx="1045" cy="432" r="3.4"/></g>
    <g>
      <circle cx="1150" cy="246" r="3.4" fill="#8fb8dc"/><circle cx="1150" cy="265" r="3.4" fill="#f2a86a"/>
      <circle cx="1150" cy="284" r="3.4" fill="#4b9a35"/><circle cx="1150" cy="302" r="3.4" fill="#d96b7a"/>
      <circle cx="1150" cy="321" r="3.4" fill="#b98fd0"/><circle cx="1150" cy="340" r="3.4" fill="#b69a94"/>
      <circle cx="1150" cy="358" r="3.4" fill="#ef9fcb"/><circle cx="1150" cy="377" r="3.4" fill="#b7b7b7"/>
      <circle cx="1150" cy="396" r="3.4" fill="var(--yellow)"/><circle cx="1150" cy="414" r="3.4" fill="#8fd7e0"/>
      <circle cx="1150" cy="432" r="3.4" fill="var(--blue)"/>
    </g>
  </svg>
</section>

<div class="export left">
  <svg width="24" height="22" viewBox="0 0 24 22"><path d="M10 4H3v16h16v-7" fill="none" stroke="currentColor" stroke-width="2"/><path d="M8 15c1-6 6-9 12-9M16 2l5 4-5 4" fill="none" stroke="currentColor" stroke-width="2"/></svg>Export</div>
<div class="export right">
  <svg width="24" height="22" viewBox="0 0 24 22"><path d="M10 4H3v16h16v-7" fill="none" stroke="currentColor" stroke-width="2"/><path d="M8 15c1-6 6-9 12-9M16 2l5 4-5 4" fill="none" stroke="currentColor" stroke-width="2"/></svg>Export</div>

<section class="table-card stats">
  <div class="thead"><div style="width:369px;border:none">Stats</div></div>
  <div class="tbody">
    <div class="trow"><div style="width:166px">Stat 1</div><div style="width:166px">0.5</div></div>
    <div class="trow"><div style="width:166px">Stat 2</div><div style="width:166px">-3</div></div>
    <div class="trow"><div style="width:166px">Stat 3</div><div style="width:166px">30%</div></div>
    <div class="trow"><div style="width:166px">Stat 4</div><div style="width:166px">0.5</div></div>
    <div class="trow"><div style="width:166px">Stat 5</div><div style="width:166px">-3</div></div>
    <div class="trow"><div style="width:166px">Stat 6</div><div style="width:166px">30%</div></div>
  </div>
  <div class="scroll"><div class="track"><div class="thumb"></div></div></div>
</section>

<section class="table-card trades">
  <div class="thead"><div style="width:166px">Open</div><div style="width:166px">Close</div><div style="width:166px">Size</div><div style="width:167px;border:none">Return</div></div>
  <div class="tbody">
    <div class="trow"><div style="width:166px">2018-04-05</div><div style="width:166px">2018-04-07</div><div style="width:166px">13</div><div style="width:133px">5%</div></div>
    <div class="trow"><div style="width:166px">2018-04-05</div><div style="width:166px">2018-04-07</div><div style="width:166px">12</div><div style="width:133px">7%</div></div>
    <div class="trow"><div style="width:166px">2018-04-05</div><div style="width:166px">2018-04-07</div><div style="width:166px">15</div><div style="width:133px">6%</div></div>
    <div class="trow"><div style="width:166px">2018-04-05</div><div style="width:166px">2018-04-07</div><div style="width:166px">16</div><div style="width:133px">9%</div></div>
    <div class="trow"><div style="width:166px">2018-04-05</div><div style="width:166px">2018-04-07</div><div style="width:166px">12</div><div style="width:133px">8%</div></div>
    <div class="trow"><div style="width:166px">2018-04-05</div><div style="width:166px">2018-04-07</div><div style="width:166px">19</div><div style="width:133px">6%</div></div>
  </div>
  <div class="scroll"><div class="track" style="left:8px"><div class="thumb"></div></div></div>
</section>

</body>
</html>
```